Business cards to launch an education platform

Hi,
I am looking at having new business cards designed.
I am a startup, developing a web platform for schools and university, the education world. It's an online assessment system.
I would like a card that looks classy, and that is using the colors and the font of my logo.

I have attached:
1) my logo
2) A business card that I have designed quickly so you can have all the information required in the card, but I really don't like it.
3) The font that I am using (Lato Regular) to design my web platform
4) Some screenshots of my web platform so you can have a look at the style that I have.

Target Market(s)

Major market: Education system: Schools and university
Minor markets: Business in general

Industry/Entity Type

Business

Contact Information for Business Card

Clara Fenwick
Director

M: 0437 518 902
E: clara.fenwick@amberLoomSystems.com.au

Requirements
Must have
• The colors of my logo

```html
<!DOCTYPE html>
<html lang="en">
<head>
<meta charset="utf-8">
<title>Amber Loom Systems — Business Cards</title>
<link href="https://fonts.googleapis.com/css2?family=Lato:wght@400;700&display=swap" rel="stylesheet">
<style>
  :root {
    --backdrop-top: #2a2a2a;
    --backdrop-bottom: #050505;
    --card-light: #f3f3f3;
    --navy: #0b3a6e;
    --royal: #0b4f9c;
    --ink: #1a1a1a;
    --back-centre: #0a7fd4;
    --back-edge: #063d7c;
    --white: #ffffff;
  }
  * { box-sizing: border-box; margin: 0; padding: 0; }
  html, body {
    width: 1200px; height: 900px; overflow: hidden;
  }
  body {
    background: linear-gradient(180deg, var(--backdrop-top) 0%, #161616 55%, var(--backdrop-bottom) 100%);
    font-family: "Lato", sans-serif;
    position: relative;
  }
  .card {
    position: absolute;
    top: 184px;
    width: 302px;
    height: 490px;
    border-radius: 13px;
    box-shadow: 0 4px 14px rgba(0,0,0,0.55);
    overflow: hidden;
  }
  .card--front {
    left: 299px;
    background: var(--card-light);
    text-align: center;
    color: var(--ink);
  }
  .card--back {
    left: 646px;
    width: 304px;
    background: radial-gradient(circle at 50% 48%, var(--back-centre) 0%, #0760b0 40%, var(--back-edge) 100%);
    color: var(--white);
    text-align: center;
  }
  .brand-mark {
    position: absolute;
    left: 50%;
    top: 42px;
    width: 78px;
    height: 78px;
    margin-left: -39px;
    background: var(--royal);
    border-radius: 4px;
  }
  .wordmark {
    position: absolute;
    left: 0; right: 0;
    color: var(--navy);
    font-weight: 400;
  }
  .wordmark__main {
    top: 160px;
    font-size: 38px;
    letter-spacing: 3px;
    line-height: 1;
  }
  .wordmark__sub {
    top: 204px;
    font-size: 23px;
    letter-spacing: 2px;
    line-height: 1;
  }
  .person {
    position: absolute;
    left: 0; right: 0;
    top: 313px;
  }
  .person__name {
    font-size: 19px;
    color: var(--royal);
    line-height: 1.1;
    text-transform: uppercase;
  }
  .person__role {
    font-size: 14px;
    line-height: 1.1;
  }
  .contact {
    position: absolute;
    left: 0; right: 0;
    top: 396px;
    font-size: 14px;
    line-height: 20px;
    list-style: none;
  }
  .contact__item {
    display: flex;
    justify-content: center;
    align-items: center;
    gap: 3px;
    white-space: nowrap;
  }
  .contact__icon { width: 11px; height: 11px; fill: var(--royal); }
  .back-wordmark {
    position: absolute;
    left: 0; right: 0;
    font-weight: 400;
  }
  .back-wordmark__main {
    top: 379px;
    font-size: 40px;
    letter-spacing: 3px;
    line-height: 1;
  }
  .back-wordmark__sub {
    top: 423px;
    font-size: 26px;
    letter-spacing: 2.5px;
    line-height: 1;
  }
</style>
</head>
<body>
  <section class="card card--front" aria-label="Business card front">
    <div class="brand-mark" aria-hidden="true"></div>
    <p class="wordmark wordmark__main">AMBER</p>
    <p class="wordmark wordmark__sub">Loom Systems</p>

    <div class="person">
      <p class="person__name">Clara Fenwick</p>
      <p class="person__role">Director</p>
    </div>

    <ul class="contact">
      <li class="contact__item">
        <svg class="contact__icon" viewBox="0 0 24 24" aria-hidden="true"><path d="M6.6 10.8a15.1 15.1 0 0 0 6.6 6.6l2.2-2.2c.3-.3.7-.4 1-.2 1.1.4 2.3.6 3.6.6.6 0 1 .4 1 1V20c0 .6-.4 1-1 1C10.6 21 3 13.4 3 4c0-.6.4-1 1-1h3.5c.6 0 1 .4 1 1 0 1.3.2 2.5.6 3.6.1.3 0 .7-.2 1z"/></svg>
        <span>0437 518 902</span>
      </li>
      <li class="contact__item">
        <svg class="contact__icon" viewBox="0 0 24 24" aria-hidden="true"><path d="M2 5h20v14H2z M2 5l10 8 10-8" /></svg>
        <span>clara.fenwick@amberLoomSystems.com.au</span>
      </li>
    </ul>
  </section>

  <section class="card card--back" aria-label="Business card back">
    <p class="back-wordmark back-wordmark__main">AMBER</p>
    <p class="back-wordmark back-wordmark__sub">Loom Systems</p>
  </section>
</body>
</html>
```